Velvet Lantern rebranding my business with a new business card

I have my new logo and now I need a refresher on my business cards. I really want something fun and fresh. I like black background or anything to make the color pop.
Logo
Name: Velvet Lantern
Contact Info as stated below:
Mira Pellow
555-013-4762
Logo
Name: Velvet Lantern
Mira Pellow
555-013-4762
fb.me/VelvetLanternbyMira
Instagram: @VelvetLanternbyMira

Industry/Entity Type

Business

Contact Information for Business Card

double-sided. Logo on one side. Contact info on the other.

Requirements
Must have
• Logo
• Name: Velvet Lantern
• Contact Info as stated below:
• Mira Pellow
• 555-013-4762
• fb.me/VelvetLanternbyMira
• fb.me/VelvetLanternbyMira

```html
<!DOCTYPE html>
<html lang="en">
<head>
<meta charset="utf-8">
<title>Velvet Lantern — Business Card</title>
<link rel="stylesheet" href="https://fonts.googleapis.com/css2?family=Roboto:wght@400;500;700&display=swap">
<style>
  :root {
    --backdrop: #e8e5e1;
    --card: #f7f7f7;
    --ink: #111111;
    --band: #000000;
    --muted: #5a5a5a;
    --rose: #f2a9bd;
    --rose-light: #f9d3de;
    --white: #ffffff;
  }
  * { margin: 0; padding: 0; box-sizing: border-box; }
  html, body {
    width: 1200px;
    height: 960px;
    overflow: hidden;
    background: var(--backdrop);
    font-family: "Roboto", Arial, sans-serif;
  }
  .canvas { position: relative; width: 1200px; height: 960px; }

  .card {
    position: absolute;
    left: 320px;
    width: 600px;
    height: 342px;
    border-radius: 18px;
    background: var(--card);
    overflow: hidden;
    box-shadow: 0 2px 6px rgba(0,0,0,0.12);
  }
  .card--front { top: 100px; }
  .card--back { top: 493px; }

  /* Front */
  .front-mark {
    position: absolute;
    left: 193px;
    top: 65px;
    width: 208px;
    height: 208px;
  }
  .front-mark__name {
    position: absolute;
    inset: 0;
    display: flex;
    align-items: center;
    justify-content: center;
    font-weight: 700;
    font-size: 21px;
    color: var(--ink);
    text-align: center;
  }
  .front-url {
    position: absolute;
    left: 0;
    right: 0;
    top: 310px;
    text-align: center;
    font-size: 15px;
    letter-spacing: 0.42em;
    color: var(--muted);
  }

  /* Back */
  .holder-name {
    position: absolute;
    right: 40px;
    top: 70px;
    font-weight: 700;
    font-size: 20px;
    color: var(--ink);
  }
  .contact-band {
    position: absolute;
    left: 0;
    right: 0;
    top: 165px;
    bottom: 0;
    background: var(--band);
  }
  .back-mark {
    position: absolute;
    left: 30px;
    bottom: 36px;
    font-weight: 700;
    font-size: 22px;
    color: var(--white);
  }
  .contact-list {
    position: absolute;
    right: 40px;
    top: 226px;
    list-style: none;
  }
  .contact-list li {
    display: flex;
    align-items: center;
    justify-content: flex-end;
    gap: 6px;
    height: 19.5px;
    font-size: 14.5px;
    color: var(--white);
  }
  .contact-list svg { width: 12px; height: 12px; flex: none; }
</style>
</head>
<body>
<main class="canvas">

  <section class="card card--front" aria-label="Card front">
    <div class="front-mark">
      <svg width="208" height="208" viewBox="0 0 208 208" aria-hidden="true">
        <circle cx="104" cy="104" r="102" fill="var(--white)" stroke="var(--ink)" stroke-width="1.5"/>
      </svg>
      <div class="front-mark__name">Velvet Lantern</div>
    </div>
    <p class="front-url">www.velvetlantern.com</p>
  </section>

  <section class="card card--back" aria-label="Card back">
    <h1 class="holder-name">MIRA PELLOW</h1>
    <div class="contact-band"></div>
    <div class="back-mark">Velvet Lantern</div>
    <ul class="contact-list">
      <li>555-013-4762
        <svg viewBox="0 0 12 12" aria-hidden="true"><path fill="#fff" d="M2.4 0.8l1.8 2.2-1 1.2c.7 1.6 2 2.9 3.6 3.6l1.2-1 2.2 1.8-.9 1.9C5.3 10.2 1.8 6.7 0.5 1.7z"/></svg>
      </li>
      <li>www.velvetlantern.com
        <svg viewBox="0 0 12 12" aria-hidden="true"><circle cx="6" cy="6" r="5.5" fill="#fff"/></svg>
      </li>
      <li>fb.me/VelvetLanternbyMira
        <svg viewBox="0 0 12 12" aria-hidden="true"><rect x="0.5" y="0.5" width="11" height="11" rx="1" fill="#fff"/></svg>
      </li>
    </ul>
  </section>

</main>
</body>
</html>
```